Residential Remodeling Contractor needs updated business card

I need a new design for my business card.
Name of the company is Ridgefell Construction. I need a card that commands presence, strength, integrity. I have been in business for 28 years. I am a Residential Remodeling Contractor that covers all aspects of a residential remodel and build.

```html
<!DOCTYPE html>
<html lang="en">
<head>
<meta charset="utf-8">
<title>Ridgefell Construction — Business Card</title>
<link href="https://fonts.googleapis.com/css2?family=Crimson+Pro:wght@700&family=Arimo:wght@400&display=swap" rel="stylesheet">
<style>
  :root {
    --navy: #173f84;
    --navy-deep: #1c3b7a;
    --ink: #3a3a3a;
    --paper: #ffffff;
    --stage: #9a9a9a;
    --pattern-light: #6f8fcf;
  }
  * { margin: 0; padding: 0; box-sizing: border-box; }
  html, body {
    width: 1200px; height: 1059px; overflow: hidden;
    background: var(--stage);
  }
  .stage { position: relative; width: 1200px; height: 1059px; }

  .card {
    position: absolute;
    width: 690px; height: 392px;
    border-radius: 15px;
    overflow: hidden;
  }
  .card--front { left: 256px; top: 89px; background: var(--paper); }
  .card--back { left: 254px; top: 569px; background: var(--navy-deep); }

  .brand-name {
    position: absolute;
    font-family: "Crimson Pro", serif;
    font-weight: 700;
    text-transform: uppercase;
    line-height: 1;
    letter-spacing: 0.5px;
  }
  .card--front .brand-name {
    left: 0; right: 0; top: 92px;
    text-align: center;
    color: var(--navy);
    font-size: 36px;
  }
  .brand-name span { display: block; }

  .holder {
    position: absolute; left: 0; right: 0; top: 190px;
    text-align: center;
  }
  .holder__name {
    font-family: "Crimson Pro", serif;
    font-weight: 700;
    font-size: 27px;
    color: var(--navy);
    letter-spacing: 0.5px;
    line-height: 1;
  }
  .holder__title {
    font-family: "Arimo", sans-serif;
    font-size: 16px;
    color: var(--ink);
    margin-top: 4px;
  }

  .divider {
    position: absolute; left: 31px; right: 31px; top: 250px;
    height: 1px; background: var(--navy);
  }

  .contacts {
    position: absolute; left: 31px; top: 264px;
    list-style: none;
    font-family: "Arimo", sans-serif;
    font-size: 16.5px;
    color: var(--ink);
  }
  .contacts li { display: flex; align-items: center; height: 24.4px; }
  .contacts svg { width: 13px; height: 13px; margin-right: 9px; fill: var(--navy); }
  .contacts .accent { color: var(--navy); }

  .address {
    position: absolute; right: 31px; top: 318px;
    text-align: right;
    font-family: "Arimo", sans-serif;
    font-size: 16.5px;
    line-height: 22px;
    color: var(--ink);
  }

  .band {
    position: absolute; left: 0; right: 0; bottom: 0;
    height: 14px; background: var(--navy);
  }

  .pattern-field {
    position: absolute; inset: 0;
    background:
      linear-gradient(200deg, var(--pattern-light) 0%, rgba(111,143,207,0.45) 30%, rgba(28,59,122,0) 60%),
      var(--navy-deep);
  }
  .card--back .brand-name {
    left: 482px; top: 290px;
    color: var(--paper);
    font-size: 22px;
  }
</style>
</head>
<body>
<main class="stage">

  <section class="card card--front" aria-label="Card front">
    <div class="brand-name"><span>Ridgefell</span><span>Construction</span></div>

    <div class="holder">
      <p class="holder__name">DALE WHITFORD</p>
      <p class="holder__title">Owner &amp; Manager</p>
    </div>

    <div class="divider"></div>

    <ul class="contacts">
      <li>
        <svg viewBox="0 0 16 16" aria-hidden="true"><path d="M1 6c0-3 3-4 7-4s7 1 7 4v1h-4V5H5v2H1zM3 8h10l2 6H1z"/></svg>
        555 014 2208
      </li>
      <li>
        <svg viewBox="0 0 16 16" aria-hidden="true"><path d="M4 0h8a1 1 0 0 1 1 1v14a1 1 0 0 1-1 1H4a1 1 0 0 1-1-1V1a1 1 0 0 1 1-1zm1 2v10h6V2zm3 11a1 1 0 1 0 0 2 1 1 0 0 0 0-2z"/></svg>
        555-014-73916
      </li>
      <li>
        <svg viewBox="0 0 16 16" aria-hidden="true"><path d="M8 1l7 5v9H1V6zm0 8L3 6v1l5 4 5-4V6z"/></svg>
        info@ridgefellconstruction.com
      </li>
      <li>
        <svg viewBox="0 0 16 16" aria-hidden="true"><circle cx="8" cy="8" r="7"/></svg>
        www.<span class="accent">ridgefellconstruction</span>.com
      </li>
    </ul>

    <address class="address" style="font-style:normal">
      P.O. Box&nbsp; Street Name<br>
      Country Name AB, A5B 521
    </address>

    <div class="band"></div>
  </section>

  <section class="card card--back" aria-label="Card back">
    <div class="pattern-field" role="img" aria-label="Repeating brand pattern fading from dark navy to light blue toward the upper right"></div>
    <div class="brand-name"><span>Ridgefell</span><span>Construction</span></div>
  </section>

</main>
</body>
</html>
```